Business Card Design needed for start up company Halvora

In need of a new business card designed for a start up company based in Sydney, Halvora is a new start up innovative Company, our mission it to make property accessible for everyday Australian and to become the leading Real Estate platform in Australia. We want it to be fresh and clean.

Industry/Entity Type

Financial

Contact Information for Business Card

Section for Name
Section for Title

HALVORA - The Strength of Pooling
Mobile:
Direct:

Font styles to use
Sans Serif

Colors
33a6d7
0692cd
0255a3
ffffff

Requirements
Must have
• Logo, all business card details

```html
<!DOCTYPE html>
<html lang="en">
<head>
<meta charset="utf-8">
<title>Halvora Business Card</title>
<link href="https://fonts.googleapis.com/css2?family=Lato:wght@400;700;900&display=swap" rel="stylesheet">
<style>
  :root {
    --sky: #33a6d7;
    --azure: #0692cd;
    --navy: #0255a3;
    --white: #ffffff;
    --paper: #f3f5f8;
    --mist: #e4e9f0;
    --stage: #e9ebee;
    --ink-soft: #5a6b80;
  }
  * { margin: 0; padding: 0; box-sizing: border-box; }
  html, body {
    width: 1200px; height: 780px; overflow: hidden;
    background: var(--stage);
    font-family: "Lato", Arial, sans-serif;
  }
  .stage {
    position: relative; width: 1200px; height: 780px;
    display: flex; align-items: center; justify-content: center; gap: 40px;
  }
  .card {
    position: relative; width: 540px; height: 309px; overflow: hidden;
    box-shadow: 0 6px 18px rgba(0,0,0,.15);
  }

  /* Front */
  .card-front {
    background: linear-gradient(160deg, var(--white) 0%, var(--paper) 100%);
  }
  .front-watermark {
    position: absolute; right: -60px; top: -120px;
    width: 300px; height: 300px; border-radius: 50%;
    background: var(--mist); opacity: .8;
  }
  .front-band {
    position: absolute; left: 0; right: 0; bottom: 0; height: 65px;
    background: linear-gradient(180deg, var(--azure), var(--sky));
  }
  .front-band-rule {
    position: absolute; left: 0; right: 0; bottom: 71px; height: 2px;
    background: var(--navy);
  }
  .logo-dot {
    position: absolute; left: 26px; top: 198px;
    width: 84px; height: 84px; border-radius: 50%;
    background: var(--azure); border: 7px solid var(--white);
    box-shadow: 0 0 0 2px var(--navy);
  }
  .brand-name {
    position: absolute; left: 122px; top: 42px;
    font-weight: 900; font-size: 60px; line-height: 1; letter-spacing: -1px;
    color: var(--navy);
  }
  .brand-tagline {
    position: absolute; left: 126px; top: 108px;
    font-weight: 400; font-size: 15px; color: var(--navy);
  }
  .person { position: absolute; left: 300px; top: 140px; }
  .person-name {
    font-weight: 900; font-size: 15px; color: var(--navy); letter-spacing: -.2px;
  }
  .person-title { font-weight: 400; font-size: 13px; color: var(--sky); }
  .contacts {
    position: absolute; left: 300px; top: 184px; list-style: none;
  }
  .contacts li {
    display: flex; align-items: center; gap: 6px;
    font-size: 12.5px; line-height: 17px; color: var(--navy);
  }
  .contact-icon { width: 13px; height: 13px; flex: none; }

  /* Back */
  .card-back {
    background: radial-gradient(ellipse at 45% 35%, #18b6e4 0%, var(--sky) 45%, var(--azure) 100%);
    display: flex; align-items: center; justify-content: center; gap: 16px;
  }
  .back-dot {
    width: 70px; height: 70px; border-radius: 50%; background: var(--white);
  }
  .back-name {
    font-weight: 900; font-size: 64px; line-height: 1; letter-spacing: -1px;
    color: var(--white);
  }
</style>
</head>
<body>
<main class="stage">
  <section class="card card-front" aria-label="Business card front">
    <div class="front-watermark"></div>
    <div class="front-band-rule"></div>
    <div class="front-band"></div>
    <div class="logo-dot"></div>
    <div class="brand-name">HALVORA</div>
    <div class="brand-tagline">The Strength of Pooling</div>
    <div class="person">
      <div class="person-name">MARA QUINLAN</div>
      <div class="person-title">Managing Director</div>
    </div>
    <ul class="contacts">
      <li>
        <svg class="contact-icon" viewBox="0 0 13 13" aria-hidden="true"><rect width="13" height="13" rx="2" fill="#33a6d7"/><rect x="4" y="2" width="5" height="9" rx="1" fill="#fff"/><rect x="5" y="3.2" width="3" height="5" fill="#33a6d7"/></svg>
        212.555.0143
      </li>
      <li>
        <svg class="contact-icon" viewBox="0 0 13 13" aria-hidden="true"><rect width="13" height="13" rx="2" fill="#33a6d7"/><path d="M3 4.5c0-1 .8-1.5 1.6-1.5l1 1.8-.8.8c.5 1 1.3 1.8 2.3 2.3l.8-.8 1.8 1c0 .8-.5 1.6-1.5 1.6C5.5 9.7 3.3 7.5 3 4.5z" fill="#fff"/></svg>
        212.555.0143
      </li>
      <li>
        <svg class="contact-icon" viewBox="0 0 13 13" aria-hidden="true"><rect width="13" height="13" rx="2" fill="#33a6d7"/><circle cx="6.5" cy="6.5" r="4" fill="none" stroke="#fff" stroke-width="1"/><ellipse cx="6.5" cy="6.5" rx="1.8" ry="4" fill="none" stroke="#fff" stroke-width=".8"/><line x1="2.5" y1="6.5" x2="10.5" y2="6.5" stroke="#fff" stroke-width=".8"/></svg>
        www.halvora-pool.com
      </li>
    </ul>
  </section>

  <section class="card card-back" aria-label="Business card back">
    <div class="back-dot"></div>
    <div class="back-name">HALVORA</div>
  </section>
</main>
</body>
</html>
```